Pinecrest Harbor Foundation Web Design

The design we need is for a WordPress blog that will be our content platform. We are a registered 501(c)3 non-profit that focuses on financially supporting the treatment of cancer patients that have been told they have no hope and there is nothing the conventional medical system can do for them. Through this wesbite we want to both rasie awareness about the treatment options plus, raise funds for treating patients. The two primary target audiences of the site are...

1. Terminally ill patients and their families to let them know that there is an option other then hospice and that we are hear to support that option.

2. People looking to help donate to a worthwhile cause that resonates with them.

The website is https://pinecrestharborfoundation.org/

See attached logo designs!!!

Target Market(s)

Cancer patients and their families

Industry/Entity Type

Foundation

Font styles to use
Sans Serif

Colors
ffffff
fbed22

Requirements
Must have
• I like this look of this site. It is clean, simple, helpful, soft. I like the flow of the pages.
• http://www.meadowsforcalm.org/
• I like the design and flow but NOT the color or boldness
• https://tvbn-youth.org/
• I like this style for a donation page.
• https://www.tumorstudyhub.org/we-are-tsh/join-the-cause/donations/one-time-donation
• with the addition of a Would you like your employer to match? button.
Nice to have
• White black and gold - but soft
• Even possibly grayscale like the site I like.

```html
<!DOCTYPE html>
<html lang="en">
<head>
<meta charset="utf-8">
<title>Pinecrest Harbor Foundation</title>
<link href="https://fonts.googleapis.com/css2?family=Roboto:ital,wght@0,400;0,500;0,700;1,400&family=Roboto+Condensed:wght@400;700&family=Open+Sans:ital,wght@0,400;0,600;1,400&display=swap" rel="stylesheet">
<style>
:root{
  --gold:#dcb84c;
  --gold-light:#e9c95e;
  --ink:#222222;
  --text:#555555;
  --muted:#777777;
  --white:#ffffff;
  --line:#e3e3e3;
  --pale:#f3f3f3;
  --footer:#6e6e6e;
  --footer-dark:#666666;
  --slate:#2b3036;
}
*{box-sizing:border-box;margin:0;padding:0}
html,body{width:1200px;height:2761px;overflow:hidden}
body{background:var(--white);font-family:"Open Sans",Arial,sans-serif;color:var(--text)}
.wrap{width:1004px;margin-left:98px;position:relative}
a{color:inherit;text-decoration:none}

/* header */
.site-header{height:127px;position:relative;border-bottom:1px solid var(--line)}
.brand{position:absolute;left:98px;top:30px;display:flex;align-items:center;gap:14px}
.brand-dot{width:44px;height:44px;border-radius:50%;background:var(--gold)}
.brand-name{font-family:"Roboto Condensed",Arial,sans-serif;font-weight:700;font-size:24px;line-height:26px;color:var(--ink);width:190px}
.header-top{position:absolute;right:98px;top:22px;display:flex;align-items:center;gap:28px}
.phone{display:flex;align-items:center;gap:12px;font-family:"Roboto",Arial,sans-serif;font-size:21px;color:#444}
.btn{display:inline-block;background:var(--gold);color:var(--white);font-family:"Roboto",Arial,sans-serif;font-weight:500;text-transform:uppercase}
.btn-donate-top{font-size:14px;padding:11px 14px;border-radius:2px}
.main-nav{position:absolute;right:98px;top:82px;display:flex;gap:26px;font-family:"Roboto",Arial,sans-serif;font-weight:500;font-size:15px;color:var(--ink)}

/* hero */
.hero{height:513px;position:relative;background:linear-gradient(180deg,#c9c6c2 0%,#b7b4b0 38%,#7d8690 52%,#a49584 70%,#8a7866 100%)}
.hero-copy{position:absolute;left:98px;top:128px}
.hero-title{font-family:"Roboto",Arial,sans-serif;font-weight:700;font-size:49px;line-height:53px;color:var(--white);text-transform:uppercase}
.btn-involved{margin-top:20px;font-size:15px;padding:12px 24px}
.hero-arrows{margin-top:26px;display:flex;gap:6px}

/* mission */
.mission{height:345px;text-align:center;padding-top:68px}
.section-title{font-family:"Roboto",Arial,sans-serif;font-weight:500;font-size:34px;color:var(--ink);text-transform:uppercase}
.mission p{width:790px;margin:28px auto 0;font-size:14.5px;line-height:26px;color:var(--muted)}
.btn-donate{margin-top:32px;font-size:17px;padding:9px 26px;border-radius:2px}

/* what we do */
.services{height:521px;position:relative;background:linear-gradient(180deg,#1f2329 0%,#3a4048 45%,#2a2f36 100%);text-align:center;padding-top:50px}
.services .section-title{color:var(--white)}
.cards{position:absolute;left:98px;top:206px;width:1004px;display:flex;justify-content:space-between}
.card{width:315px;background:var(--white);position:relative;padding:74px 24px 28px;box-shadow:0 2px 8px rgba(0,0,0,.3)}
.card.featured{margin-top:0;padding-bottom:18px}
.card-icon{position:absolute;left:50%;top:-58px;margin-left:-56px;width:112px;height:112px;border-radius:50%;background:var(--gold);border:5px solid var(--white);display:flex;align-items:center;justify-content:center}
.card h3{font-family:"Roboto",Arial,sans-serif;font-weight:400;font-size:21px;color:var(--ink)}
.card p{margin-top:14px;font-size:11.5px;line-height:22px;color:var(--text)}
.read-more{display:inline-block;margin-top:16px;border:1px solid #888;border-radius:14px;font-size:10px;padding:3px 12px;color:#444;text-transform:uppercase}

/* events */
.events{height:546px;position:relative}
.events-col{position:absolute;top:72px;left:98px;width:545px}
.video-col{position:absolute;top:72px;left:696px;width:406px}
.col-title{font-family:"Roboto Condensed",Arial,sans-serif;font-size:26px;color:var(--ink);text-transform:uppercase}
.event{display:flex;gap:22px;margin-top:45px;padding-bottom:14px;border-bottom:1px solid var(--line);width:545px}
.event+.event{margin-top:28px}
.event-img{width:173px;height:153px;flex:none}
.event-img.a{background:linear-gradient(135deg,#6e5a4c,#d9d3cc)}
.event-img.b{background:linear-gradient(135deg,#c9c2b8,#5e6f86)}
.event h4{font-family:"Roboto",Arial,sans-serif;font-weight:400;font-size:19px;color:var(--ink);margin-top:4px}
.event-meta{margin-top:14px;font-size:10px;color:var(--gold);text-transform:uppercase}
.event p{margin-top:12px;font-size:12px;line-height:22px;color:var(--text)}
.video{margin-top:40px;box-shadow:0 2px 6px rgba(0,0,0,.25)}
.video-frame{height:288px;background:linear-gradient(180deg,#e2ddd2 0%,#cdd2c4 45%,#4d8dc0 62%,#5b7d43 100%)}
.video-bar{height:26px;background:#e8e8e8;display:flex;align-items:center;gap:10px;padding:0 10px;font-size:8px;color:#666}
.progress{flex:1;height:3px;background:#999;position:relative}
.progress span{position:absolute;left:0;top:0;height:3px;width:45%;background:#d9534f}

/* testimonial */
.testimonial{height:289px;background:var(--pale);position:relative}
.quote{position:absolute;left:128px;top:54px;width:720px;font-style:italic;font-size:13.5px;line-height:25px;color:#555}
.quote cite{display:block;margin-top:12px;font-size:15.5px;color:var(--ink)}
.dots{position:absolute;left:128px;top:182px;display:flex;gap:4px}
.dots span{width:22px;height:3px;background:#ddd}
.dots span:first-child{background:var(--gold)}
.avatar{position:absolute;left:889px;top:40px;width:180px;height:180px;border-radius:50%;background:radial-gradient(circle at 50% 45%,#e8c3a6,#a9b6c2 75%);border:4px solid var(--white)}

/* footer */
.site-footer{height:351px;background:var(--footer);color:var(--white);position:relative;font-family:"Open Sans",Arial,sans-serif}
.fcol{position:absolute;top:80px}
.fcol h5{font-family:"Roboto Condensed",Arial,sans-serif;font-weight:400;font-size:17px;text-transform:uppercase}
.contact{left:98px;width:300px}
.contact li{list-style:none;display:flex;gap:16px;margin-top:24px;font-size:12.5px;line-height:22px}
.contact li:first-child{margin-top:28px}
.signup{left:436px;width:286px;top:76px}
.signup p{margin-top:20px;font-size:11px;line-height:20px}
.signup .field{margin-top:12px;height:40px;background:var(--white);color:#888;font-size:11px;padding:12px 14px}
.btn-subscribe{margin-top:10px;font-size:12px;font-weight:700;padding:12px 14px;color:#333}
.links{left:808px;top:76px}
.links li{list-style:none;font-size:12px;line-height:24px}
.links ul{margin-top:16px}
.social{left:1001px;top:76px}
.social li{list-style:none;display:flex;align-items:center;gap:10px;margin-top:12px;font-size:14px}
.social ul{margin-top:8px}
.social .ic{width:26px;height:26px;border-radius:50%;border:1.5px solid var(--white)}
.copyright{position:absolute;left:0;top:2692px;width:1200px;height:69px;background:var(--footer-dark);border-top:1px solid #7c7c7c;color:var(--white);font-size:12px;text-align:center;line-height:66px}
</style>
</head>
<body>

<header class="site-header">
  <div class="brand"><span class="brand-dot"></span><span class="brand-name">Pinecrest Harbor Foundation</span></div>
  <div class="header-top">
    <span class="phone">
      <svg width="20" height="20" viewBox="0 0 24 24"><path d="M6.6 10.8a15.1 15.1 0 0 0 6.6 6.6l2.2-2.2a1 1 0 0 1 1-.25 11.4 11.4 0 0 0 3.6.57 1 1 0 0 1 1 1V20a1 1 0 0 1-1 1A17 17 0 0 1 3 4a1 1 0 0 1 1-1h3.5a1 1 0 0 1 1 1c0 1.25.2 2.45.57 3.57a1 1 0 0 1-.25 1z" fill="#dcb84c"/></svg>
      (08) 5550 1482
    </span>
    <a class="btn btn-donate-top" href="#">Donate now +</a>
  </div>
  <nav class="main-nav">
    <a href="#">HOME</a><a href="#">ABOUT US</a><a href="#">SERVICES</a><a href="#">OUR VISION</a><a href="#">DONATE</a><a href="#">BLOG</a><a href="#">CONTACT US</a>
  </nav>
</header>

<section class="hero" role="img" aria-label="Photo of a person standing with arms outstretched on a beach at sunset">
  <div class="hero-copy">
    <h1 class="hero-title">Pinecrest<br>Harbor<br>Foundation</h1>
    <a class="btn btn-involved" href="#">Get involved</a>
    <div class="hero-arrows">
      <svg width="40" height="24" viewBox="0 0 40 24"><path d="M12 4 4 12l8 8M28 4l8 8-8 8" stroke="#fff" stroke-width="2.5" fill="none"/></svg>
    </div>
  </div>
</section>

<section class="mission">
  <h2 class="section-title">Our Mission</h2>
  <p>Sed ut perspiciatis unde omnis iste natus error sit voluptatem accusantium doloremque laudantium, totam rem aperiam, eaque ipsa quae ab illo inventore veritatis et quasi architecto beatae vitae dicta sunt explicabo. Nemo enim ipsam voluptatem quia voluptas sit aspernatur aut odit aut fugit, sed quia consequuntur</p>
  <a class="btn btn-donate" href="#">DONATE</a>
</section>

<section class="services" role="img" aria-label="Dark mountain landscape photo behind the services">
  <h2 class="section-title">What We Do</h2>
  <div class="cards">
    <div class="card">
      <div class="card-icon"><svg width="46" height="46" viewBox="0 0 24 24"><circle cx="12" cy="12" r="8" fill="none" stroke="#fff" stroke-width="2"/><path d="M12 4v16M7 9h10M7 15h10" stroke="#fff" stroke-width="1.5"/></svg></div>
      <h3>Quis autem vel eum iure</h3>
      <p>Sed ut perspiciatis unde omnis iste natus error sit voluptatem accusantium doloremque laudantium, totam rem aperiam, eaque ipsa quae ab illo inventore veritatis et quasi architecto</p>
    </div>
    <div class="card featured">
      <div class="card-icon"><svg width="46" height="46" viewBox="0 0 24 24"><path d="M12 3c-2.5 0-3.5 2-3 4l3 5 3-5c.5-2-.5-4-3-4zM12 12l-5 9M12 12l5 9" stroke="#fff" stroke-width="2.2" fill="none" stroke-linecap="round"/></svg></div>
      <h3>Cancer Patients</h3>
      <p>Sed ut perspiciatis unde omnis iste natus error sit voluptatem accusantium doloremque laudantium, totam rem aperiam, eaque ipsa quae ab illo inventore veritatis et quasi architecto</p>
      <a class="read-more" href="#">Read more &#8857;</a>
    </div>
    <div class="card">
      <div class="card-icon"><svg width="46" height="46" viewBox="0 0 24 24"><path d="M12 21 4 13a5 5 0 0 1 8-6 5 5 0 0 1 8 6z" fill="none" stroke="#fff" stroke-width="2"/></svg></div>
      <h3>Quis autem vel eum iure</h3>
      <p>Sed ut perspiciatis unde omnis iste natus error sit voluptatem accusantium doloremque laudantium, totam rem aperiam, eaque ipsa quae ab illo inventore veritatis et quasi architecto</p>
    </div>
  </div>
</section>

<section class="events">
  <div class="events-col">
    <h2 class="col-title">Upcoming Events</h2>
    <article class="event">
      <div class="event-img a" role="img" aria-label="Photo of a coffee cup beside a tablet"></div>
      <div>
        <h4>Nemo Enim Ipsam Voluptatem</h4>
        <div class="event-meta">3 minutes ago &nbsp; / &nbsp; 0 comments</div>
        <p>Lorem ipsum dolor sit amet, consectetur adipiscing elit, sed do eiusmod tempor incididunt ut labore et dolore magna aliqua. Ut enim ad minim veniam, quis nostrud</p>
      </div>
    </article>
    <article class="event">
      <div class="event-img b" role="img" aria-label="Photo of volunteers holding a community sign"></div>
      <div>
        <h4>Nemo Enim Ipsam Voluptatem</h4>
        <div class="event-meta">3 minutes ago &nbsp; / &nbsp; 0 comments</div>
        <p>Lorem ipsum dolor sit amet, consectetur adipiscing elit, sed do eiusmod tempor incididunt ut labore et dolore magna aliqua. Ut enim ad minim veniam, quis nostrud</p>
      </div>
    </article>
  </div>
  <div class="video-col">
    <h2 class="col-title">Pinecrest Harbor Foundation</h2>
    <div class="video">
      <div class="video-frame" role="img" aria-label="Video still of a group of volunteers in blue shirts standing in a park"></div>
      <div class="video-bar">
        <svg width="8" height="10" viewBox="0 0 8 10"><path d="M0 0l8 5-8 5z" fill="#333"/></svg>
        <span>00:00/00:00</span>
        <div class="progress"><span></span></div>
        <svg width="12" height="10" viewBox="0 0 12 10"><path d="M0 3h3l4-3v10L3 7H0z" fill="#333"/></svg>
        <div class="progress" style="flex:0 0 40px"><span style="width:80%"></span></div>
      </div>
    </div>
  </div>
</section>

<section class="testimonial">
  <blockquote class="quote">&#8220; Sed ut perspiciatis unde omnis iste natus error sit voluptatem accusantium doloremque laudantium, totam rem aperiam, eaque ipsa quae ab illo inventore veritatis et quasi architecto beatae vitae dicta sunt explicabo. Nemo enim ipsam voluptatem quia voluptas sit aspernatur aut odit aut fugit, sed quia consequuntur
    <cite>Ellis Morrow - Pinecrest Harbor Foundation</cite>
  </blockquote>
  <div class="dots"><span></span><span></span><span></span></div>
  <div class="avatar" role="img" aria-label="Portrait photo of a smiling supporter"></div>
</section>

<footer class="site-footer">
  <div class="fcol contact">
    <h5>Contact Us</h5>
    <ul>
      <li><svg width="16" height="20" viewBox="0 0 16 20"><path d="M8 1a6 6 0 0 0-6 6c0 5 6 12 6 12s6-7 6-12a6 6 0 0 0-6-6z" fill="none" stroke="#fff" stroke-width="1.5"/><circle cx="8" cy="7" r="2" fill="#fff"/></svg><span>Pinecrest Harbor Foundation<br>4820 LB, Harrowmere The Netherlands.</span></li>
      <li><svg width="16" height="16" viewBox="0 0 24 24"><path d="M6.6 10.8a15.1 15.1 0 0 0 6.6 6.6l2.2-2.2a1 1 0 0 1 1-.25 11.4 11.4 0 0 0 3.6.57 1 1 0 0 1 1 1V20a1 1 0 0 1-1 1A17 17 0 0 1 3 4a1 1 0 0 1 1-1h3.5a1 1 0 0 1 1 1c0 1.25.2 2.45.57 3.57a1 1 0 0 1-.25 1z" fill="none" stroke="#fff" stroke-width="1.8"/></svg><span>Phone : (408) 555-0193</span></li>
      <li><svg width="16" height="14" viewBox="0 0 16 14"><rect x="1" y="1" width="14" height="12" fill="none" stroke="#fff" stroke-width="1.3"/><path d="M1 1l7 6 7-6" fill="none" stroke="#fff" stroke-width="1.3"/></svg><span>info@pinecrestharborfoundation.org</span></li>
    </ul>
  </div>
  <div class="fcol signup">
    <h5>Sign up to receive email</h5>
    <p>Excepteur sint occaecat cupidatat non proident, sunt in culpa qui Nemo enim ipsam voluptatem</p>
    <div class="field">Enter Name</div>
    <a class="btn btn-subscribe" href="#">SUBSCRIBE</a>
  </div>
  <div class="fcol links">
    <h5>Quick Links</h5>
    <ul><li>Home</li><li>About Us</li><li>Services</li><li>Our Vision</li><li>donate</li><li>Blog</li><li>Contact Us</li></ul>
  </div>
  <div class="fcol social">
    <h5>Social Media</h5>
    <ul>
      <li><span class="ic"></span>Circlenet</li>
      <li><span class="ic"></span>Chirpline</li>
      <li><span class="ic"></span>Plusroom</li>
      <li><span class="ic"></span>Reelhall</li>
    </ul>
  </div>
</footer>
<div class="copyright">Copyright &copy; Pinecrest Harbor Foundation 2017. All rights reserved.</div>

</body>
</html>
```